Black Matte card with samurai logo which I would like it to be textured and company name on one side and on the other side I would like the company information with the reno (Face logo) Sushi logo. Double Sided card.

majority customers are University students, University sororities and fraternities.

It Company

Reno Sushi
317 W. Harlow Ave
Tucson, AZ 85042
Phone (520)413-6271
Fax (520)357-1846
E-mail: Renosushidesert@mailbox-example.com
FB: Renosushidesert
Twitter: Renosushidesert

• Present Normal

```html
<!DOCTYPE html>
<html lang="en">
<head>
<meta charset="utf-8">
<title>Reno Sushi – Business Card</title>
<link href="https://fonts.googleapis.com/css2?family=Open+Sans:wght@400;600&display=swap" rel="stylesheet">
<style>
  :root {
    --stage: #e9e6e1;
    --card-black: #1c1c1c;
    --ink-black: #231f20;
    --paper: #ffffff;
    --accent-red: #b3282d;
    --text-dark: #2a2a2a;
    --text-light: #ffffff;
  }
  * { box-sizing: border-box; margin: 0; padding: 0; }
  html, body {
    width: 1200px; height: 369px; overflow: hidden;
    background: var(--stage);
    font-family: "Open Sans", Arial, sans-serif;
  }
  .canvas { position: relative; width: 1200px; height: 369px; }
  .card {
    position: absolute; top: 29px; width: 545px; height: 312px;
    overflow: hidden;
  }
  .card--front { left: 38px; background: var(--card-black); }
  .card--back { left: 617px; background: var(--paper); border: 1px solid #cfcfcf; }

  /* Front */
  .front-mark {
    position: absolute; left: 0; right: 0; top: 92px;
    display: flex; flex-direction: column; align-items: center; gap: 14px;
  }
  .front-mark__dot {
    width: 30px; height: 30px; border-radius: 50%; background: var(--accent-red);
  }
  .front-mark__name {
    color: var(--text-light); font-size: 44px; font-weight: 600; letter-spacing: 1px;
  }
  .front-web {
    position: absolute; left: 0; right: 0; top: 267px; text-align: center;
    color: var(--text-light); font-size: 15px; letter-spacing: 1.6px;
  }

  /* Back */
  .back-mark {
    position: absolute; left: 38px; top: 58px;
    display: flex; flex-direction: column; align-items: center; gap: 12px;
    width: 140px;
  }
  .back-mark__dot {
    width: 22px; height: 22px; border-radius: 50%; background: var(--accent-red);
  }
  .back-mark__name {
    color: var(--accent-red); font-size: 30px; font-weight: 400; line-height: 1.1; text-align: center;
  }
  .address {
    position: absolute; right: 26px; top: 16px; text-align: right;
    color: var(--text-dark); font-size: 13px; line-height: 20px;
  }
  .swoosh { position: absolute; left: 0; top: 0; width: 545px; height: 312px; }
  .contacts {
    position: absolute; right: 22px; top: 191px; list-style: none;
    color: var(--text-light); font-size: 13px;
  }
  .contacts li {
    display: flex; justify-content: flex-end; align-items: center; gap: 7px;
    height: 20.5px;
  }
  .contacts svg { width: 11px; height: 11px; flex: none; }
  .social-square { width: 11px; height: 11px; background: #6d8cc7; flex: none; }
</style>
</head>
<body>
<main class="canvas">

  <section class="card card--front" aria-label="Card front">
    <div class="front-mark">
      <span class="front-mark__dot"></span>
      <span class="front-mark__name">Reno Sushi</span>
    </div>
    <p class="front-web">www.renosushidesert.com</p>
  </section>

  <section class="card card--back" aria-label="Card back">
    <svg class="swoosh" viewBox="0 0 545 312" aria-hidden="true">
      <path d="M0,282 C120,300 210,255 300,205 C385,160 455,152 545,150 L545,312 L0,312 Z" fill="var(--ink-black)"/>
      <path d="M0,246 C110,292 205,238 300,188 C385,146 460,136 545,138 L545,150 C455,150 385,162 300,202 C205,250 110,298 0,262 Z" fill="var(--accent-red)"/>
    </svg>

    <div class="back-mark">
      <span class="back-mark__dot"></span>
      <span class="back-mark__name">reno sushi</span>
    </div>

    <address class="address" style="font-style:normal">
      Reno Sushi 317<br>
      W. Harlow Ave Tucson<br>
      AZ 85042
    </address>

    <ul class="contacts">
      <li>
        <svg viewBox="0 0 12 12"><path d="M3 1 L5 3.5 L4 5 Q5 7 7 8 L8.5 7 L11 9 L9.5 11 Q4 10.5 1 3 Z" fill="#fff"/></svg>
        <span>(520)413-6271</span>
      </li>
      <li>
        <svg viewBox="0 0 12 12"><rect x="3" y="0.5" width="6" height="11" rx="1" fill="#fff"/><rect x="4" y="2" width="4" height="5" fill="var(--ink-black)"/></svg>
        <span>(520)357-1846</span>
      </li>
      <li><span class="social-square"></span><span>Renosushidesert</span></li>
      <li><span class="social-square"></span><span>Renosushidesert</span></li>
      <li>
        <svg viewBox="0 0 12 12"><rect x="0.5" y="2.5" width="11" height="7.5" fill="#fff"/><path d="M0.5 2.5 L6 7 L11.5 2.5" stroke="var(--ink-black)" fill="none"/></svg>
        <span>Renosushidesert@mailbox-example.com</span>
      </li>
    </ul>
  </section>

</main>
</body>
</html>
```